Boutique Store Selling Antiques and Unique Finds

I need a Web Page designed for my Store Called "Willow Lane". I would like a very classic, muted design that looks European when pulled up. I will be selling Antiques from all over the world and Unique finds that have reproduced. I will also be selling high-end purses and jewelry with unique, reasonable products for the every-day buyer as well.

Target Market(s)

25-70 year old men and women;)

Coding

Coded - Design and coding required

Number of Pages Required

1 page

Colors

Designer to choose only greyscale colors for use in the design.

Requirements
Must have
• I want it

```html
<!DOCTYPE html>
<html lang="en">
<head>
<meta charset="utf-8">
<title>Willow Lane – Antiques and Unique Finds</title>
<link href="https://fonts.googleapis.com/css2?family=Libre+Caslon+Text:wght@400&family=Lato:wght@400;700&display=swap" rel="stylesheet">
<style>
:root{
  --cream:#f6ebd1;
  --cream-light:#f4ead6;
  --ink:#231f1c;
  --line:#3a332c;
  --label:#efe7db;
  --frame:#b9b2a6;
  --white:#ffffff;
}
*{margin:0;padding:0;box-sizing:border-box}
html,body{width:1200px;height:2784px;overflow:hidden}
body{background:var(--cream);color:var(--ink);font-family:"Lato",sans-serif;position:relative}
.abs{position:absolute}
.serif{font-family:"Libre Caslon Text",serif}

/* header */
.topbar{top:44px;font-size:14.5px;display:flex;align-items:center;gap:8px;letter-spacing:.1px}
.brand{left:0;width:1200px;top:26px;display:flex;justify-content:center;align-items:center;gap:10px}
.brand-dot{width:14px;height:14px;border-radius:50%;background:var(--ink)}
.brand-name{font-family:"Libre Caslon Text",serif;font-size:24px;letter-spacing:4px;text-transform:uppercase;color:var(--ink)}
.rule{left:109px;width:979px;top:107px;height:1px;background:var(--line)}
.rule-active{left:109px;width:51px;top:106px;height:3px;background:var(--ink)}
.nav{left:112px;width:976px;top:130px;display:flex;justify-content:space-between;font-size:15px;text-transform:uppercase;list-style:none}

/* hero */
.hero{left:0;top:176px;width:1200px;height:600px;background:radial-gradient(circle at 80% 30%,#8a6a3a 0%,#4a3422 30%,#2a1d14 70%),#2d2018}
.hero-frame{left:111px;top:356px;width:554px;height:266px;background:var(--frame);opacity:.9}
.hero-card{left:120px;top:364px;width:537px;height:250px;background:var(--cream-light);border:1px solid #8f877b;text-align:center}
.hero-title{font-family:"Libre Caslon Text",serif;font-size:54px;margin-top:30px;letter-spacing:.5px}
.hero-sub{font-size:15px;margin-top:14px}
.btn{display:inline-block;margin-top:22px;width:145px;height:45px;line-height:42px;background:var(--white);font-size:14px;font-weight:700;border-right:3px solid var(--ink);border-bottom:3px solid var(--ink)}
.arrow{width:44px;height:44px;border-radius:50%;background:var(--white);top:457px;display:flex;align-items:center;justify-content:center}

/* sections */
.mark-dot{width:12px;height:12px;border-radius:50%;background:var(--ink);left:594px}
.section-title{left:0;width:1200px;text-align:center;font-family:"Libre Caslon Text",serif;font-size:36px;text-transform:uppercase}
.box{border:1px solid var(--line)}
.vline{width:1px;background:var(--line)}
.photo{position:absolute}
.label{position:absolute;background:var(--label);opacity:.95;text-align:center;font-family:"Libre Caslon Text",serif;font-size:19px;line-height:56px;text-transform:uppercase}
.shop-title{left:457px;top:1365px;width:287px;height:51px;background:var(--ink);color:var(--cream);text-align:center;line-height:51px;font-family:"Libre Caslon Text",serif;font-size:34px}
.card-head{position:absolute;width:477px;text-align:center;font-family:"Libre Caslon Text",serif;font-size:22px;line-height:23px;text-transform:uppercase}

/* footer */
.footer{left:0;top:2434px;width:1200px;height:350px;background:var(--ink);color:var(--cream)}
.footer-ring{left:544px;top:2385px;width:112px;height:112px;border-radius:50%;background:var(--ink);display:flex;align-items:center;justify-content:center}
.footer-ring span{width:90px;height:90px;border-radius:50%;background:var(--cream);display:block}
.f-head{top:2522px;font-size:21px}
.f-list{top:2566px;font-size:14.5px;line-height:28px;list-style:none}
.social{top:2574px;left:944px;display:flex;gap:26px}
.social span{width:12px;height:12px;border-radius:50%;background:var(--cream)}
.pay{top:2709px;left:111px;display:flex;gap:5px}
.pay span{width:37px;height:23px;background:var(--white);border-radius:2px}
.copy{top:2712px;right:112px;font-size:14.5px}
</style>
</head>
<body>

<header>
  <div class="abs topbar" style="left:112px">
    <svg width="12" height="12" viewBox="0 0 24 24"><path fill="#231f1c" d="M6.6 10.8a15 15 0 0 0 6.6 6.6l2.2-2.2a1 1 0 0 1 1-.25 11 11 0 0 0 3.6.6 1 1 0 0 1 1 1V20a1 1 0 0 1-1 1A17 17 0 0 1 3 4a1 1 0 0 1 1-1h3.5a1 1 0 0 1 1 1c0 1.2.2 2.4.6 3.6a1 1 0 0 1-.25 1z"/></svg>
    <span>CALL US TODAY : +1 555 014 2277</span>
  </div>
  <div class="abs brand"><span class="brand-dot"></span><span class="brand-name">Willow Lane</span></div>
  <div class="abs topbar" style="left:787px">
    <svg width="11" height="12" viewBox="0 0 22 24"><circle cx="11" cy="7" r="6" fill="#231f1c"/><path fill="#231f1c" d="M0 24c0-7 5-10 11-10s11 3 11 10z"/></svg>
    <span>SIGN IN OR REGISTER</span>
  </div>
  <div class="abs topbar" style="left:1000px">
    <svg width="13" height="12" viewBox="0 0 26 24"><path fill="#231f1c" d="M0 1h5l1 3h20l-3 10H8zM9 19a2.5 2.5 0 1 0 .01 0zM21 19a2.5 2.5 0 1 0 .01 0z"/></svg>
    <span>(0) ITEMS</span>
  </div>
  <div class="abs rule"></div>
  <div class="abs rule-active"></div>
  <ul class="abs nav">
    <li>Home</li><li>Sale</li><li>New Arrivals</li><li>Antique &amp; Vintage</li><li>Art</li><li>Furnishing</li><li>Seating</li><li>Accessory</li><li>Outdoor</li><li>Lighting</li>
  </ul>
</header>

<section>
  <div class="abs hero" role="img" aria-label="Still life of antiques: typewriter, brass fan, bellows camera and leather cases"></div>
  <div class="abs hero-frame"></div>
  <div class="abs hero-card">
    <h1 class="hero-title">WILLOW LANE</h1>
    <p class="hero-sub">We are a Boutique Store Selling Antiques and Unique Finds</p>
    <span class="btn">SHOP NOW</span>
  </div>
  <div class="abs arrow" style="left:32px"><svg width="12" height="20" viewBox="0 0 12 20"><path d="M10 2 2 10l8 8" fill="none" stroke="#231f1c" stroke-width="2.4"/></svg></div>
  <div class="abs arrow" style="left:1121px"><svg width="12" height="20" viewBox="0 0 12 20"><path d="m2 2 8 8-8 8" fill="none" stroke="#231f1c" stroke-width="2.4"/></svg></div>
</section>

<section>
  <span class="abs mark-dot" style="top:840px"></span>
  <h2 class="abs section-title" style="top:862px">New Arrivals</h2>
  <div class="abs box" style="left:97px;top:922px;width:1006px;height:373px"></div>
  <div class="abs vline" style="left:434px;top:922px;height:373px"></div>
  <div class="abs vline" style="left:767px;top:922px;height:373px"></div>
  <div class="photo" style="left:111px;top:938px;width:311px;height:343px;background:linear-gradient(180deg,#b9a583,#6b5330 45%,#3a3430)" role="img" aria-label="Jewelled antique brass crown on a stand"></div>
  <div class="photo" style="left:445px;top:938px;width:310px;height:343px;background:linear-gradient(180deg,#8a7048,#d9d3c8 40%,#9a8664 70%,#3d3835)" role="img" aria-label="Ornate gilded crown with blue stones"></div>
  <div class="photo" style="left:778px;top:938px;width:311px;height:343px;background:linear-gradient(180deg,#d8d2c6,#9b8354 45%,#3a2a1e 65%,#6a4a2c)" role="img" aria-label="Gold crown resting on antique books"></div>
  <div class="label" style="left:131px;top:955px;width:273px">Nemo Enim Ipsam</div>
  <div class="label" style="left:464px;top:955px;width:273px">Nemo Enim Ipsam</div>
  <div class="label" style="left:797px;top:955px;width:273px">Nemo Enim Ipsam</div>
</section>

<section>
  <span class="abs mark-dot" style="top:1338px"></span>
  <div class="abs box" style="left:97px;top:1391px;width:1006px;height:949px"></div>
  <div class="abs" style="left:97px;top:1881px;width:1006px;height:1px;background:var(--line)"></div>
  <h2 class="abs shop-title">SHOP ONLINE</h2>

  <h3 class="card-head" style="left:111px;top:1442px">Lorem ipsum dolor sit amet,<br>consectetur</h3>
  <h3 class="card-head" style="left:611px;top:1442px">Lorem ipsum dolor sit amet,<br>consectetur</h3>
  <div class="photo" style="left:111px;top:1506px;width:477px;height:359px;background:linear-gradient(180deg,#cfd0cc,#b7b3aa 55%,#8c6a4a 80%,#a9a49c)" role="img" aria-label="Vintage desk, chair, shelf and teddy bear against a grey wall"></div>
  <div class="photo" style="left:611px;top:1506px;width:477px;height:359px;background:radial-gradient(circle at 30% 40%,#9a7a40,#3a2516 50%,#1e1410)" role="img" aria-label="Antique brass mantel clock on a wooden table"></div>

  <h3 class="card-head" style="left:111px;top:1899px">Lorem ipsum dolor sit amet,<br>consectetur</h3>
  <h3 class="card-head" style="left:611px;top:1899px">Lorem ipsum dolor sit amet,<br>consectetur</h3>
  <div class="photo" style="left:111px;top:1962px;width:477px;height:360px;background:radial-gradient(circle at 45% 50%,#9a7c55,#4a3626 55%,#2a1e16)" role="img" aria-label="Pocket watch on an old leather book and map"></div>
  <div class="photo" style="left:611px;top:1962px;width:477px;height:360px;background:linear-gradient(135deg,#8a4a3a,#4a3428 40%,#6a5848 70%,#9a948a)" role="img" aria-label="Gramophone horn and antique furniture at a market stall"></div>
</section>

<footer>
  <div class="abs footer"></div>
  <div class="abs footer-ring"><span></span></div>
  <h4 class="abs f-head" style="left:111px;color:var(--cream);font-weight:400">Our Company</h4>
  <p class="abs f-list" style="left:113px;color:var(--cream)">Lorem ipsum dolor sit amet, turipiscing<br>elit, sed do eiusmod tempor incididunt ut<br>labore et dolorealiqua</p>
  <h4 class="abs f-head" style="left:498px;color:var(--cream);font-weight:400">Links</h4>
  <ul class="abs f-list" style="left:500px;color:var(--cream)"><li>Home</li><li>Product</li><li>Blog</li><li>Contact</li></ul>
  <h4 class="abs f-head" style="left:695px;color:var(--cream);font-weight:400">Legal</h4>
  <ul class="abs f-list" style="left:697px;color:var(--cream)"><li>Faq</li><li>Privacy Policy</li><li>Terms &amp; Conditions</li></ul>
  <h4 class="abs f-head" style="left:944px;color:var(--cream);font-weight:400">Follow Us</h4>
  <div class="abs social"><span></span><span></span><span></span><span></span></div>
  <div class="abs pay"><span></span><span></span><span></span><span></span><span></span><span></span><span></span><span></span></div>
  <p class="abs copy" style="color:var(--cream)">© Copyrights.2021 Willow Lane Antiques.All Rights Reserved</p>
</footer>

</body>
</html>
```